Web Design Project

Website Design Brief

Company Details
1a) Name of Company

MAPLEHAVEN
1) What is the nature of your business?: Briefly describe your products or services:

INDEPENDENT CONTEMPORARY TRADITIONAL ITALIAN RESTAURANT IN THE HEART OF ELMSWORTH QUAY ALSO CATERING FOR PRIVATE CORPORATE EVENTS AND WEDDING RECEPTIONS

1a) Who is your target market? Who are you hoping to reach with your site?

CITY CORPORATES, LOCAL CORPORATES/BUSINESSES, LOCAL RESIDENTS, VISITORS TO THE DOCK, LOCAL HOTELS

Website Details
1b) Do you have an existing website? If so, what is the URL?
HTTP://WWW.MAPLEHAVENTRATTORIA.EXAMPLE

2b) IMPORTANT: Please list at least 3 URLs (web addresses) of high quality sites that you like the look of (these do not have to be sites who’s business is similar to yours. It aids us in determining what your design style is.) Please consider layout, colours, navigation, graphics, and typography.

http://www.thecorvelle.example/

http://www.dunmorrow.example/

http://www.pavokitchen.example/

http://www.ilfaro.example/

3b) What colours or colour schemes would you like?

WHITE, BLACK, SILVER/ALUMINIUM (PLS LOOK AT OUR OUTSIDE CHAIRS)

4b) List the Navigation links for your Site:

5b) What type of look are you trying to achieve? (e.g. clean, high-tech, conservative, warm, flashy, etc.)

SIMPLE ELEGANT CLASSY INFORMATIVE, EASY TO USE, A REFLECTION OF THE BUSINESS ITSELF

6b) Please provide the addresses of competitors' sites, if possible:

Do not contact the client direct - all questions should go through Brightwell Venues - info@brightwellvenues.example
Updates

thanks for the designs that I have received so far. I have these general comments:

- please avoid using icons for phones or paperclips etc 
- use dummy text (one design used text from another website) 
- there won't any live social media feeds to the site
the client likes a lot of the designs that this company comes up with: 

i look forward to see some more designs

hi all, 

further to my last update, here are a few more pointers:
- there will be no search facilities - so no "search" box please 
- please just use the images supplied - no stock ones
- use just the page names give (no other pages) 

The client is looking for a simple, elegant design. 

Many thanks 
Rolf 

thanks for all the designs. 

I have uploaded another file to the brief which shows some posters that the client particularly likes. Perhaps the homepage could consist of large rectangle made up of a number of boxes - for some introductory text, a large image, mailing list, contact details, Lunch Special etc - just an idea! 
It's clear that the client likes clean lines with square edges. 
I want to be able to pass the designs directly onto the client so can designers avoid adding extra info or page. For example one design has a tab for a "Gift Card" - it will be easier for me if such additions are avoided. 

thanks!                                                                                                                                                                                                                                                                                                                                                                                                    

Thank you for all your designs - please keep them coming! 

hi all,

I am meeting the client tomorrow afternoon so please submit revisions / designs before then. 

Many thanks, 
Rolf

Target Market(s)

Business people, upmarket etc

Industry/Entity Type

Business

Requirements
Must have
• - The home page needs a slide show of images as well as:
- a mailing list form - very simple, "Join our mailing list - name, email"
- 3 or 4 sentences of text
- facebook link

```html
<!DOCTYPE html>
<html lang="en">
<head>
<meta charset="utf-8">
<title>Maplehaven Italian</title>
<link rel="stylesheet" href="https://fonts.googleapis.com/css2?family=Noto+Sans:wght@400;700&family=Ubuntu:wght@400;500;700&display=swap">
<style>
:root{
  --wood-dark:#1e140e;
  --wood-mid:#3a281c;
  --panel:rgba(14,11,9,.88);
  --nav-top:#f7f7f7;
  --nav-bottom:#d6d6d6;
  --ink:#222;
  --white:#fff;
  --heading:#e6e6e6;
  --body-text:#a8a8a8;
  --muted:#8c8c8c;
  --field:#1c1c1c;
  --field-line:#2e2e2e;
  --button-top:#fdfdfd;
  --button-bottom:#d2d2d2;
  --social:#5c6f8c;
}
*{box-sizing:border-box;margin:0;padding:0}
html,body{width:934px;height:1200px;overflow:hidden}
body{
  position:relative;
  font-family:"Noto Sans",sans-serif;
  background:linear-gradient(90deg,var(--wood-mid),var(--wood-dark) 30%,#2d1f16 60%,var(--wood-dark) 85%,var(--wood-mid));
  color:var(--body-text);
}
.abs{position:absolute}
.column{left:102px;top:0;width:729px;height:975px;background:var(--panel)}
.footer-panel{left:102px;top:990px;width:729px;height:195px;background:var(--panel)}

.brand{left:125px;top:22px;color:var(--white);font-weight:400;text-align:center;width:296px}
.brand-name{font-size:50px;line-height:62px;letter-spacing:1px}
.brand-tag{font-size:17px;letter-spacing:5px;line-height:22px}

.book-tab{left:737px;top:0;width:75px;height:52px;background:#ececec;color:var(--ink);
  font-size:14px;line-height:18px;text-align:center;padding-top:5px;
  clip-path:polygon(0 0,100% 0,100% 100%,50% 88%,0 100%)}

.nav{left:0;top:130px;width:934px;height:53px;background:linear-gradient(var(--nav-top),var(--nav-bottom))}
.nav a{position:absolute;top:0;height:53px;line-height:53px;font-size:14px;color:var(--ink);text-decoration:none;text-align:center;border-left:1px solid #c4c4c4}
.nav a.active{top:9px;height:36px;line-height:36px;background:linear-gradient(#3a3a3a,#050505);color:var(--white);border-radius:4px;border:none}

.slider{left:110px;top:191px;width:714px;height:330px;overflow:hidden}
.slide-photo{left:0;top:0;width:714px;height:330px;background:linear-gradient(135deg,#6a5238,#c9bba0 45%,#8c7355 70%,#3a2b1e)}
.slide-caption{left:487px;top:0;width:227px;height:330px;background:rgba(20,20,20,.85);border-radius:8px 0 0 8px;color:var(--white);padding:56px 0 0 27px}
.slide-caption .lead{font-family:"Ubuntu",sans-serif;font-size:30px;line-height:34px}
.slide-caption .big{font-family:"Ubuntu",sans-serif;font-size:41px;line-height:40px}
.slide-caption .sub{font-size:14px;margin-top:4px;line-height:20px}
.slide-caption .venue{font-size:18px;line-height:22px}
.dots{left:621px;top:297px}
.dots span{display:inline-block;width:12px;height:12px;border-radius:50%;background:#888;margin-right:5px}
.dots span.on{background:#eee}

.btn{position:absolute;background:linear-gradient(var(--button-top),var(--button-bottom));color:var(--ink);
  border:1px solid #999;border-radius:3px;font-size:13px;font-weight:700;text-align:center;box-shadow:0 6px 6px -4px rgba(255,255,255,.12)}

h2{position:absolute;font-family:"Ubuntu",sans-serif;font-weight:500;color:var(--heading);font-size:22px;line-height:26px;text-shadow:0 1px 2px #000}
.intro{left:117px;top:574px;width:405px;font-size:10px;line-height:18px}
.intro strong{color:var(--white);font-size:10.5px}
.label{position:absolute;left:117px;color:#ddd;font-size:13px}
.field{position:absolute;left:117px;width:405px;background:var(--field);border:1px solid var(--field-line);border-radius:3px}

.event-img{position:absolute;left:544px;width:100px;height:90px;border:2px solid #ddd}
.event-title{position:absolute;left:651px;color:var(--white);font-size:13px;font-weight:700}
.event-text{position:absolute;left:651px;width:168px;font-size:10px;line-height:15px;text-align:justify}
.event-more{position:absolute;right:115px;font-size:11px;font-weight:700;color:var(--muted);text-decoration:underline}

.thumb{position:absolute;width:63px;height:51px;border:2px solid #ddd}
.contact-name{left:414px;top:1030px;color:var(--white);font-size:20px;line-height:22px}
.contact-tag{left:440px;top:1053px;color:var(--white);font-size:7px;letter-spacing:3px}
.address{left:415px;top:1068px;font-size:9px;line-height:17.5px;color:var(--muted)}
.social{position:absolute;top:1032px;width:26px;height:26px;border-radius:50%;background:var(--social)}
.copyright{left:656px;top:1121px;font-size:9px;line-height:17.5px;color:var(--muted)}
</style>
</head>
<body>
<div class="abs column"></div>
<div class="abs footer-panel"></div>

<header>
  <div class="abs brand"><div class="brand-name">Maplehaven</div><div class="brand-tag">ITALIAN</div></div>
  <div class="abs book-tab">BOOK A<br>TABLE</div>
</header>

<nav class="abs nav">
  <a class="active" style="left:117px;width:106px">WELCOME</a>
  <a style="left:232px;width:140px;border-left:none">OUR RESTAURANT</a>
  <a style="left:372px;width:96px">OUR MENU</a>
  <a style="left:468px;width:84px">GALLERY</a>
  <a style="left:552px;width:75px">EVENTS</a>
  <a style="left:627px;width:109px">RESERVATION</a>
  <a style="left:736px;width:84px">CONTACT</a>
</nav>

<section class="abs slider">
  <div class="abs slide-photo" role="img" aria-label="Restaurant dining room with laid tables and wine glasses"></div>
  <div class="abs slide-caption">
    <div class="lead">FREE VENUE</div>
    <div class="big">HIRE!</div>
    <div class="sub">Book your next event at</div>
    <div class="venue">Maplehaven Italian</div>
  </div>
  <div class="btn" style="left:598px;top:197px;width:86px;height:26px;line-height:24px">Read More</div>
  <div class="abs dots"><span class="on"></span><span></span><span></span><span></span></div>
</section>

<section>
  <h2 style="left:117px;top:543px">Welcome to MaplehavenItalian</h2>
  <p class="abs intro"><strong>Koleacene anrit ma haselurta ertyusera deyuas lertya.</strong><br>Cum socis natoqu et magnis dist monte senasc ridiculmue feugiata lesuada lecenas ac seuis ultricies pharcnaleda dertyas nec sit ameorem etuer adipiscing elauris ferment. Ut tellus dolor, dapibus eget, elementum vel, cursus eleifelitas. Aenean auctor wisi et urna. Aliquamat volutpatis ac turpis. Integer rutrum ante eu lacus.</p>
  <div class="btn" style="left:433px;top:669px;width:87px;height:26px;line-height:24px">Read More</div>

  <h2 style="left:117px;top:704px">Mail Us</h2>
  <span class="label" style="top:734px">Name</span>
  <div class="field" style="top:754px;height:22px"></div>
  <span class="label" style="top:780px">Email Address</span>
  <div class="field" style="top:800px;height:22px"></div>
  <span class="label" style="top:831px">Message</span>
  <div class="field" style="top:851px;height:55px"></div>
  <div class="btn" style="left:433px;top:919px;width:87px;height:26px;line-height:24px">Send Mail</div>
</section>

<section>
  <h2 style="left:542px;top:543px">Events</h2>

  <div class="event-img" style="top:575px;background:linear-gradient(135deg,#e8e2da,#8a7a6a)" role="img" aria-label="Guests raising glasses at a corporate event"></div>
  <div class="event-title" style="top:572px">Corporate Events</div>
  <p class="event-text" style="top:589px">Cum socis natoqu et magnis dist monte senasc ridiculmue feugiata lesuada.........</p>
  <span class="event-more" style="top:651px">Read More</span>

  <div class="event-img" style="top:697px;background:linear-gradient(135deg,#d8d4cc,#8c8478)" role="img" aria-label="Banquet hall set for a wedding reception"></div>
  <div class="event-title" style="top:694px">Wedding Receptions</div>
  <p class="event-text" style="top:711px">Cum socis natoqu et magnis dist monte senasc ridiculmue feugiata lesuada.........</p>
  <span class="event-more" style="top:773px">Read More</span>

  <div class="event-img" style="top:819px;background:linear-gradient(135deg,#cfc8bc,#5a5048)" role="img" aria-label="Private dining room with laid tables"></div>
  <div class="event-title" style="top:816px">Private Hire</div>
  <p class="event-text" style="top:833px">Cum socis natoqu et magnis dist monte senasc ridiculmue feugiata lesuada.........</p>
  <span class="event-more" style="top:895px">Read More</span>
</section>

<footer>
  <h2 style="left:117px;top:997px">Gallery</h2>
  <div class="thumb" style="left:117px;top:1032px;background:linear-gradient(#3a2a1c,#7a5a30)" role="img" aria-label="Restaurant exterior at night"></div>
  <div class="thumb" style="left:194px;top:1032px;background:linear-gradient(#6a3a2a,#c8a890)" role="img" aria-label="Lounge interior"></div>
  <div class="thumb" style="left:271px;top:1032px;background:linear-gradient(#b8c4cc,#8a7a60)" role="img" aria-label="Quayside view"></div>
  <div class="thumb" style="left:117px;top:1100px;background:linear-gradient(#d8d4d0,#4a3a30)" role="img" aria-label="Plated starter"></div>
  <div class="thumb" style="left:194px;top:1100px;background:linear-gradient(#e8d8b0,#b07a40)" role="img" aria-label="Plated main course"></div>
  <div class="thumb" style="left:271px;top:1100px;background:linear-gradient(#e0c8b8,#c0503a)" role="img" aria-label="Plated seafood dish"></div>

  <h2 style="left:413px;top:997px">Contact Us</h2>
  <div class="abs contact-name">Maplehaven</div>
  <div class="abs contact-tag">ITALIAN</div>
  <p class="abs address">12 Harbour Row,<br>Elmsworth,<br>EL4 2QX<br>Telephone : 020 7946 0321<br>Email : info@maplehaventrattoria.example</p>

  <h2 style="left:656px;top:997px">Follow Us</h2>
  <a class="social" style="left:657px" aria-label="Social profile 1"></a>
  <a class="social" style="left:690px" aria-label="Social profile 2"></a>
  <a class="social" style="left:723px" aria-label="Social profile 3"></a>
  <a class="social" style="left:756px" aria-label="Social profile 4"></a>
  <p class="abs copyright">Copyright © 2012 Maplehaven Italian<br>All Rights Reserved. &nbsp;/ &nbsp;Privacy Policy</p>
</footer>
</body>
</html>
```